QuillVane needs a dashboard page designed

Redesign the dashboard shown in the provided images.

There are two images:
- dashboard.png
- dashboard-expanded.png

NOTE: The vocabulary navigation on the left will be a very long list of words 100s, so keep that in mind when you're designing both the vocab navigation and the expanded vocab popup.

In the dashboard.png picture, there needs to be a progress chart showing the word progress like the following: review 1(show it as completed) -> review 2(show the user they are here) -> review 3(unvisited) -> review 4(unvisited)

The do-not-design-this-page.png image is for your reference only. It is not to be designed. Use it to understand the overall look and feel of the website to help you create the best dashboard page possible.
Updates

Need extra days to review

Industry/Entity Type

Education English learning

Number of Pages Required

1 page

Requirements
Must have
• The main navigation and main header cannot change between pages. See the do-not-design page for the main navigateion and header.
Should not have
• Do not add a person profile. We will not have images of our users. Keep the icons in the main navigation as they are.

```html
<!DOCTYPE html>
<html lang="en">
<head>
<meta charset="utf-8">
<title>QuillVane – Vocabulary Dashboard</title>
<link href="https://fonts.googleapis.com/css2?family=Plus+Jakarta+Sans:wght@400;500;600;700&display=swap" rel="stylesheet">
<style>
:root{
  --stage:#b1b1b1;
  --ink:#1f2328;
  --ink-soft:#555a61;
  --rail:#252a30;
  --rail-active:#3a4149;
  --header:#23272c;
  --panel:#ffffff;
  --main:#f5f6f8;
  --line:#e6e8ec;
  --brand:#2b5aa8;
  --brand-soft:#eef3fb;
  --step-off:#dcdde0;
  --step-off-text:#a3a6ab;
  --purple:#6a4cf5;
  --orange:#ffa52b;
  --blue:#1e88e5;
  --red:#f0305c;
  --gold:#f2a900;
}
*{box-sizing:border-box;margin:0;padding:0}
html,body{width:933px;height:1200px;overflow:hidden}
body{background:var(--stage);font-family:"Plus Jakarta Sans",sans-serif;color:var(--ink);position:relative}
.frame{position:absolute;left:30px;width:1440px;height:915px;transform:scale(0.6056);transform-origin:0 0;background:var(--main);overflow:hidden}
.frame--main{top:30px}
.frame--popup{top:614px}
.abs{position:absolute}

.topbar{left:0;top:0;width:1440px;height:35px;background:var(--header);color:#fff}
.topbar__title{position:absolute;left:674px;top:8px;font-size:14px;font-weight:500}
.topbar__icons{position:absolute;right:14px;top:7px;display:flex;gap:20px;align-items:center}
.rail{left:0;top:0;width:78px;height:915px;background:var(--rail)}
.rail__item{position:absolute;left:0;width:78px;height:70px;color:#fff;font-size:9px;text-align:center;padding-top:20px}
.rail__item svg{display:block;margin:0 auto 3px}
.rail__item--active{background:var(--rail-active)}

.vocab{left:78px;top:35px;width:283px;height:862px;background:var(--panel);border-right:1px solid var(--line)}
.vocab__head{position:absolute;left:12px;right:16px;top:22px;display:flex;justify-content:space-between;font-size:16px;font-weight:500}
.vocab__expand{color:var(--brand)}
.vocab__row{position:absolute;left:0;width:283px;height:44px;padding:0 20px;display:flex;align-items:center;justify-content:space-between;font-size:16px;font-weight:500;border-bottom:1px solid var(--line)}
.vocab__row--word{background:var(--brand-soft);font-weight:400;font-size:15px;height:40px;border:0}

.step{width:50px;height:50px;border-radius:50%;display:flex;align-items:center;justify-content:center;font-size:19px;top:60px}
.step--done{background:var(--brand)}
.step--now{background:#fff;border:1.5px solid var(--brand);color:var(--ink)}
.step--todo{background:var(--step-off);color:var(--step-off-text)}
.step-line{top:84px;height:1.5px;background:var(--step-off)}
.step-line--done{background:var(--brand)}
.step-label{top:124px;font-size:16px;font-weight:500;width:100px;text-align:center}
.step-label--todo{color:var(--step-off-text)}

.word-title{left:394px;top:184px;font-size:27px;font-weight:700;display:flex;gap:12px;align-items:center}
.cta{left:1083px;top:177px;width:342px;height:46px;border-radius:23px;background:var(--rail);color:#fff;font-size:16px;font-weight:600;display:flex;align-items:center;justify-content:center;gap:12px}
.lede{left:394px;top:260px;width:1030px;font-size:14px;line-height:24px;color:var(--ink-soft)}

.chart{left:394px;top:355px;width:1030px;height:388px;background:#fff;border:1px solid var(--line);border-radius:20px}
.chart__badge{position:absolute;left:24px;top:23px;width:48px;height:48px;border-radius:50%;background:#edf1f8;display:flex;align-items:center;justify-content:center}
.chart__title{position:absolute;left:83px;top:36px;font-size:18px;font-weight:600}
.chart__tabs{position:absolute;left:657px;top:27px;height:40px;width:347px;border-radius:20px;background:#f3f4f6;display:flex;align-items:center;padding:0 4px;font-size:14px;font-weight:500;color:#444}
.chart__tabs span{padding:0 12px}
.chart__tabs .is-on{background:#fff;border-radius:16px;padding:8px 12px;color:var(--ink);font-weight:600;margin-left:auto}
.legend{position:absolute;left:44px;font-size:14px;font-weight:500}
.grid{position:absolute;left:282px;width:725px;height:1px;background:#eef0f2}
.bar{position:absolute;width:32px;border-radius:16px 16px 0 0;bottom:57px}
.month{position:absolute;top:343px;width:40px;text-align:center;font-size:12px;color:#444}

.analysis-title{left:394px;top:782px;font-size:18px;font-weight:600}
.analysis-text{left:394px;top:823px;width:1030px;font-size:14px;line-height:24px;color:var(--ink-soft)}

.scrim{left:0;top:0;width:1440px;height:915px;background:rgba(20,22,26,.52)}
.modal{left:467px;top:250px;width:506px;height:415px;background:#fff;border-radius:8px}
.modal__title{position:absolute;left:24px;top:26px;font-size:21px;font-weight:600}
.modal__close{position:absolute;left:454px;top:24px;width:28px;height:28px;border-radius:50%;background:#fde3e6;display:flex;align-items:center;justify-content:center}
.acc{position:absolute;left:24px;width:458px;background:#f5f6f8;border-radius:6px;overflow:hidden}
.acc__head{height:57px;display:flex;align-items:center;padding:0 14px 0 12px;gap:14px;font-size:17px;font-weight:600}
.acc__icon{width:34px;height:34px;border-radius:6px;background:#fff;display:flex;align-items:center;justify-content:center}
.acc__chev{margin-left:auto}
.chips{padding:4px 12px 0}
.chips__row{display:flex;flex-wrap:nowrap;gap:7px;margin-bottom:10px}
.chip{height:31px;padding:0 11px;border:1px solid #e0e2e6;background:#fff;border-radius:16px;font-size:12.5px;letter-spacing:-0.2px;white-space:nowrap;display:flex;align-items:center}
</style>
</head>
<body>

<!-- Frame 1: dashboard -->
<section class="frame frame--main">
  <div class="abs topbar">
    <div class="topbar__title">Daily English ▾</div>
    <div class="topbar__icons">
      <svg width="20" height="20" viewBox="0 0 20 20"><circle cx="10" cy="10" r="6.5" fill="none" stroke="#fff" stroke-width="3.5" stroke-dasharray="3 2"/><circle cx="10" cy="10" r="3" fill="#fff"/></svg>
      <svg width="20" height="20" viewBox="0 0 20 20"><path d="M10 2l7 3v5c0 4-3 7-7 8-4-1-7-4-7-8V5z" fill="#fff"/><path d="M6.5 10l2.5 2.5 4.5-5" stroke="#23272c" stroke-width="2" fill="none"/></svg>
      <svg width="34" height="22" viewBox="0 0 34 22"><circle cx="11" cy="11" r="10" fill="#fff"/><circle cx="11" cy="8" r="3.5" fill="#23272c"/><path d="M4.5 17c2-4 11-4 13 0" fill="#23272c"/><path d="M26 9l3 3 3-3" stroke="#fff" stroke-width="1.6" fill="none"/></svg>
    </div>
  </div>
  <nav class="abs rail">
    <div class="rail__item rail__item--active" style="top:35px"><svg width="18" height="16" viewBox="0 0 18 16"><path d="M9 1l8 7h-2v7h-4v-4H7v4H3V8H1z" fill="#fff"/></svg>QuillVane</div>
    <div class="rail__item" style="top:110px"><svg width="22" height="20" viewBox="0 0 22 20"><path d="M2 5l6-2 6 2 6-2v12l-6 2-6-2-6 2z" fill="#fff"/><circle cx="11" cy="6" r="3" fill="#252a30"/></svg>Daily English</div>
    <div class="rail__item" style="top:190px"><svg width="16" height="20" viewBox="0 0 16 20"><rect x="1" y="1" width="14" height="18" fill="#fff"/><g fill="#252a30"><rect x="4" y="4" width="3" height="3"/><rect x="9" y="4" width="3" height="3"/><rect x="4" y="9" width="3" height="3"/><rect x="9" y="9" width="3" height="3"/><rect x="6" y="14" width="4" height="5"/></g></svg>Business</div>
  </nav>
  <aside class="abs vocab">
    <div class="vocab__head"><span>All &nbsp;⌵</span><span class="vocab__expand">Expand</span></div>
    <div class="vocab__row" style="top:63px"><span>Short-Term Memory</span><svg width="18" height="10"><path d="M1 9l8-7 8 7" stroke="#777" fill="none" stroke-width="1.5"/></svg></div>
    <div class="vocab__row vocab__row--word" style="top:107px">Grab</div>
    <div class="vocab__row" style="top:147px"><span>Working Memory</span><svg width="18" height="10"><path d="M1 1l8 7 8-7" stroke="#777" fill="none" stroke-width="1.5"/></svg></div>
    <div class="vocab__row" style="top:191px"><span>Long-Term Memory</span><svg width="18" height="10"><path d="M1 1l8 7 8-7" stroke="#777" fill="none" stroke-width="1.5"/></svg></div>
  </aside>

  <div class="abs step-line step-line--done" style="left:427px;width:161px"></div>
  <div class="abs step-line" style="left:587px;width:805px"></div>
  <div class="abs step step--done" style="left:402px"><svg width="22" height="22" viewBox="0 0 22 22"><circle cx="11" cy="11" r="9" fill="none" stroke="#fff" stroke-width="1.6"/><path d="M7 11l3 3 5-6" stroke="#fff" stroke-width="1.8" fill="none"/></svg></div>
  <div class="abs step step--now" style="left:562px">2</div>
  <div class="abs step step--todo" style="left:723px">3</div>
  <div class="abs step step--todo" style="left:884px">4</div>
  <div class="abs step step--todo" style="left:1045px">5</div>
  <div class="abs step step--todo" style="left:1206px">6</div>
  <div class="abs step step--todo" style="left:1367px">7</div>
  <div class="abs step-label" style="left:377px">Review 1</div>
  <div class="abs step-label" style="left:537px">Review 1</div>
  <div class="abs step-label step-label--todo" style="left:698px">Review 1</div>
  <div class="abs step-label step-label--todo" style="left:859px">Review 1</div>
  <div class="abs step-label step-label--todo" style="left:1020px">Review 1</div>
  <div class="abs step-label step-label--todo" style="left:1181px">Review 1</div>
  <div class="abs step-label step-label--todo" style="left:1342px">Review 1</div>

  <h1 class="abs word-title">Grab <svg width="22" height="22" viewBox="0 0 22 22"><path d="M11 1l3 6.5 7 .8-5.2 4.8 1.4 7L11 16.6 4.8 20l1.4-7L1 8.3l7-.8z" fill="var(--gold)"/></svg></h1>
  <div class="abs cta"><svg width="20" height="20" viewBox="0 0 20 20"><circle cx="10" cy="10" r="10" fill="#fff"/><path d="M8 6l6 4-6 4z" fill="#252a30"/></svg>Start Vocabulary Review Exercise 3</div>
  <p class="abs lede">The word "grab" is most commonly used as a verb, meaning to take something quickly or suddenly. Imagine you're running late for school. You don't have time for breakfast, so you quickly grab an apple from the kitchen and rush out the door. As you reach the bus stop, your friend waves and says, "Hey! Let's grab a coffee after class." Later, when you sit down, your phone starts ringing. You grab it from your bag and answer.</p>

  <div class="abs chart">
    <div class="chart__badge"><svg width="22" height="20" viewBox="0 0 22 20"><path d="M2 2v16h18" stroke="var(--brand)" stroke-width="2" fill="none"/><path d="M5 14V9h3v5M10 14V6h3v8M15 14v-4h3v4" stroke="var(--brand)" stroke-width="1.6" fill="none"/></svg></div>
    <div class="chart__title">Learning Curve Graph</div>
    <div class="chart__tabs"><span>1 day</span><span>1 week</span><span>1 month</span><span>1 year</span><span class="is-on">All Time</span></div>
    <div class="legend" style="top:121px;color:var(--orange)">Long-Term Memory</div>
    <div class="legend" style="top:172px;color:var(--purple)">Working Memory</div>
    <div class="legend" style="top:223px;color:var(--red)">Short-Term Memory</div>
    <div class="legend" style="top:274px;color:var(--blue)">Forgotten Memory</div>
    <div class="grid" style="top:129px"></div><div class="grid" style="top:179px"></div><div class="grid" style="top:230px"></div><div class="grid" style="top:280px"></div><div class="grid" style="top:330px"></div>
    <div class="bar" style="left:284px;height:152px;background:var(--purple)"></div>
    <div class="bar" style="left:346px;height:201px;background:var(--orange)"></div>
    <div class="bar" style="left:408px;height:48px;background:var(--blue)"></div>
    <div class="bar" style="left:470px;height:98px;background:var(--red)"></div>
    <div class="bar" style="left:532px;height:201px;background:var(--orange)"></div>
    <div class="bar" style="left:594px;height:152px;background:var(--purple)"></div>
    <div class="bar" style="left:656px;height:48px;background:var(--blue)"></div>
    <div class="bar" style="left:718px;height:98px;background:var(--red)"></div>
    <div class="bar" style="left:780px;height:201px;background:var(--orange)"></div>
    <div class="bar" style="left:842px;height:48px;background:var(--blue)"></div>
    <div class="bar" style="left:904px;height:152px;background:var(--purple)"></div>
    <div class="bar" style="left:966px;height:98px;background:var(--red)"></div>
    <span class="month" style="left:280px">Jan</span><span class="month" style="left:342px">Feb</span><span class="month" style="left:404px">Mar</span><span class="month" style="left:466px">Apr</span><span class="month" style="left:528px">May</span><span class="month" style="left:590px">Jun</span><span class="month" style="left:652px">Jul</span><span class="month" style="left:714px">Aug</span><span class="month" style="left:776px">Sep</span><span class="month" style="left:838px">Oct</span><span class="month" style="left:900px">Nov</span><span class="month" style="left:962px">Dec</span>
  </div>

  <h2 class="abs analysis-title">QuillVane Learning Analysis</h2>
  <p class="abs analysis-text">Lorem ipsum dolor sit amet, consectetur adipiscing elit, sed do eiusmod tempor incididunt ut labore et dolore magna aliqua. Ut enim ad minim veniam, quis nostrud exercitation ullamco laboris nisi ut aliquip ex ea commodo consequat.</p>
</section>

<!-- Frame 2: dashboard with vocabulary popup -->
<section class="frame frame--popup">
  <div class="abs topbar">
    <div class="topbar__title">Daily English ▾</div>
    <div class="topbar__icons">
      <svg width="20" height="20" viewBox="0 0 20 20"><circle cx="10" cy="10" r="6.5" fill="none" stroke="#fff" stroke-width="3.5" stroke-dasharray="3 2"/><circle cx="10" cy="10" r="3" fill="#fff"/></svg>
      <svg width="20" height="20" viewBox="0 0 20 20"><path d="M10 2l7 3v5c0 4-3 7-7 8-4-1-7-4-7-8V5z" fill="#fff"/><path d="M6.5 10l2.5 2.5 4.5-5" stroke="#23272c" stroke-width="2" fill="none"/></svg>
      <svg width="34" height="22" viewBox="0 0 34 22"><circle cx="11" cy="11" r="10" fill="#fff"/><circle cx="11" cy="8" r="3.5" fill="#23272c"/><path d="M4.5 17c2-4 11-4 13 0" fill="#23272c"/><path d="M26 9l3 3 3-3" stroke="#fff" stroke-width="1.6" fill="none"/></svg>
    </div>
  </div>
  <nav class="abs rail">
    <div class="rail__item rail__item--active" style="top:35px"><svg width="18" height="16" viewBox="0 0 18 16"><path d="M9 1l8 7h-2v7h-4v-4H7v4H3V8H1z" fill="#fff"/></svg>QuillVane</div>
    <div class="rail__item" style="top:110px"><svg width="22" height="20" viewBox="0 0 22 20"><path d="M2 5l6-2 6 2 6-2v12l-6 2-6-2-6 2z" fill="#fff"/><circle cx="11" cy="6" r="3" fill="#252a30"/></svg>Daily English</div>
    <div class="rail__item" style="top:190px"><svg width="16" height="20" viewBox="0 0 16 20"><rect x="1" y="1" width="14" height="18" fill="#fff"/><g fill="#252a30"><rect x="4" y="4" width="3" height="3"/><rect x="9" y="4" width="3" height="3"/><rect x="4" y="9" width="3" height="3"/><rect x="9" y="9" width="3" height="3"/><rect x="6" y="14" width="4" height="5"/></g></svg>Business</div>
  </nav>
  <aside class="abs vocab">
    <div class="vocab__head"><span>All &nbsp;⌵</span><span class="vocab__expand">Expand</span></div>
    <div class="vocab__row" style="top:63px"><span>Short-Term Memory</span><svg width="18" height="10"><path d="M1 9l8-7 8 7" stroke="#777" fill="none" stroke-width="1.5"/></svg></div>
    <div class="vocab__row vocab__row--word" style="top:107px">Grab</div>
    <div class="vocab__row" style="top:147px"><span>Working Memory</span><svg width="18" height="10"><path d="M1 1l8 7 8-7" stroke="#777" fill="none" stroke-width="1.5"/></svg></div>
    <div class="vocab__row" style="top:191px"><span>Long-Term Memory</span><svg width="18" height="10"><path d="M1 1l8 7 8-7" stroke="#777" fill="none" stroke-width="1.5"/></svg></div>
  </aside>

  <div class="abs step-line step-line--done" style="left:427px;width:161px"></div>
  <div class="abs step-line" style="left:587px;width:805px"></div>
  <div class="abs step step--done" style="left:402px"><svg width="22" height="22" viewBox="0 0 22 22"><circle cx="11" cy="11" r="9" fill="none" stroke="#fff" stroke-width="1.6"/><path d="M7 11l3 3 5-6" stroke="#fff" stroke-width="1.8" fill="none"/></svg></div>
  <div class="abs step step--now" style="left:562px">2</div>
  <div class="abs step step--todo" style="left:723px">3</div>
  <div class="abs step step--todo" style="left:884px">4</div>
  <div class="abs step step--todo" style="left:1045px">5</div>
  <div class="abs step step--todo" style="left:1206px">6</div>
  <div class="abs step step--todo" style="left:1367px">7</div>
  <div class="abs step-label" style="left:377px">Review 1</div>
  <div class="abs step-label" style="left:537px">Review 1</div>
  <div class="abs step-label step-label--todo" style="left:698px">Review 1</div>
  <div class="abs step-label step-label--todo" style="left:859px">Review 1</div>
  <div class="abs step-label step-label--todo" style="left:1020px">Review 1</div>
  <div class="abs step-label step-label--todo" style="left:1181px">Review 1</div>
  <div class="abs step-label step-label--todo" style="left:1342px">Review 1</div>

  <h1 class="abs word-title">Grab <svg width="22" height="22" viewBox="0 0 22 22"><path d="M11 1l3 6.5 7 .8-5.2 4.8 1.4 7L11 16.6 4.8 20l1.4-7L1 8.3l7-.8z" fill="var(--gold)"/></svg></h1>
  <div class="abs cta"><svg width="20" height="20" viewBox="0 0 20 20"><circle cx="10" cy="10" r="10" fill="#fff"/><path d="M8 6l6 4-6 4z" fill="#252a30"/></svg>Start Vocabulary Review Exercise 3</div>
  <p class="abs lede">The word "grab" is most commonly used as a verb, meaning to take something quickly or suddenly. Imagine you're running late for school. You don't have time for breakfast, so you quickly grab an apple from the kitchen and rush out the door. As you reach the bus stop, your friend waves and says, "Hey! Let's grab a coffee after class." Later, when you sit down, your phone starts ringing. You grab it from your bag and answer.</p>

  <div class="abs chart">
    <div class="chart__badge"><svg width="22" height="20" viewBox="0 0 22 20"><path d="M2 2v16h18" stroke="var(--brand)" stroke-width="2" fill="none"/><path d="M5 14V9h3v5M10 14V6h3v8M15 14v-4h3v4" stroke="var(--brand)" stroke-width="1.6" fill="none"/></svg></div>
    <div class="chart__title">Learning Curve Graph</div>
    <div class="chart__tabs"><span>1 day</span><span>1 week</span><span>1 month</span><span>1 year</span><span class="is-on">All Time</span></div>
    <div class="legend" style="top:121px;color:var(--orange)">Long-Term Memory</div>
    <div class="legend" style="top:172px;color:var(--purple)">Working Memory</div>
    <div class="legend" style="top:223px;color:var(--red)">Short-Term Memory</div>
    <div class="legend" style="top:274px;color:var(--blue)">Forgotten Memory</div>
    <div class="grid" style="top:129px"></div><div class="grid" style="top:179px"></div><div class="grid" style="top:230px"></div><div class="grid" style="top:280px"></div><div class="grid" style="top:330px"></div>
    <div class="bar" style="left:284px;height:152px;background:var(--purple)"></div>
    <div class="bar" style="left:346px;height:201px;background:var(--orange)"></div>
    <div class="bar" style="left:408px;height:48px;background:var(--blue)"></div>
    <div class="bar" style="left:470px;height:98px;background:var(--red)"></div>
    <div class="bar" style="left:532px;height:201px;background:var(--orange)"></div>
    <div class="bar" style="left:594px;height:152px;background:var(--purple)"></div>
    <div class="bar" style="left:656px;height:48px;background:var(--blue)"></div>
    <div class="bar" style="left:718px;height:98px;background:var(--red)"></div>
    <div class="bar" style="left:780px;height:201px;background:var(--orange)"></div>
    <div class="bar" style="left:842px;height:48px;background:var(--blue)"></div>
    <div class="bar" style="left:904px;height:152px;background:var(--purple)"></div>
    <div class="bar" style="left:966px;height:98px;background:var(--red)"></div>
    <span class="month" style="left:280px">Jan</span><span class="month" style="left:342px">Feb</span><span class="month" style="left:404px">Mar</span><span class="month" style="left:466px">Apr</span><span class="month" style="left:528px">May</span><span class="month" style="left:590px">Jun</span><span class="month" style="left:652px">Jul</span><span class="month" style="left:714px">Aug</span><span class="month" style="left:776px">Sep</span><span class="month" style="left:838px">Oct</span><span class="month" style="left:900px">Nov</span><span class="month" style="left:962px">Dec</span>
  </div>

  <h2 class="abs analysis-title">QuillVane Learning Analysis</h2>
  <p class="abs analysis-text">Lorem ipsum dolor sit amet, consectetur adipiscing elit, sed do eiusmod tempor incididunt ut labore et dolore magna aliqua. Ut enim ad minim veniam, quis nostrud exercitation ullamco laboris nisi ut aliquip ex ea commodo consequat.</p>

  <div class="abs scrim"></div>
  <div class="abs modal" role="dialog" aria-label="Vocabulary list">
    <div class="modal__title">QuillVane</div>
    <div class="modal__close"><svg width="10" height="10"><path d="M1 1l8 8M9 1l-8 8" stroke="#e0263f" stroke-width="1.6"/></svg></div>
    <div class="acc" style="top:84px">
      <div class="acc__head"><span class="acc__icon"><svg width="22" height="22" viewBox="0 0 22 22"><circle cx="12" cy="12" r="7" fill="none" stroke="#333" stroke-width="1.4"/><path d="M12 8v4l3 2M10 3h4M2 10h4M1 14h4" stroke="#333" stroke-width="1.4" fill="none"/></svg></span>Short-Term Memory<svg class="acc__chev" width="18" height="10"><path d="M1 1l8 7 8-7" stroke="#777" fill="none" stroke-width="1.5"/></svg></div>
    </div>
    <div class="acc" style="top:158px;height:158px">
      <div class="acc__head"><span class="acc__icon"><svg width="22" height="22" viewBox="0 0 22 22"><path d="M4 19v-5C2 12 2 6 7 4c5-2 10 1 10 6l2 3h-2v3h-3v3" fill="none" stroke="#333" stroke-width="1.4"/><circle cx="11" cy="10" r="3" fill="none" stroke="#333" stroke-width="1.4"/></svg></span>Working Memory<svg class="acc__chev" width="18" height="10"><path d="M1 9l8-7 8 7" stroke="#777" fill="none" stroke-width="1.5"/></svg></div>
      <div class="chips">
        <div class="chips__row"><span class="chip">Cool Down</span><span class="chip">Crave</span><span class="chip">Go For</span><span class="chip">Go-To</span><span class="chip">Soothing</span></div>
        <div class="chips__row"><span class="chip">In The Mood For</span><span class="chip">Sip</span><span class="chip">Stick With</span><span class="chip">Throw In/Throw On</span></div>
      </div>
    </div>
    <div class="acc" style="top:334px">
      <div class="acc__head"><span class="acc__icon"><svg width="22" height="22" viewBox="0 0 22 22"><path d="M4 18v-5C2 11 2 6 7 4c5-2 9 1 9 5" fill="none" stroke="#333" stroke-width="1.4"/><rect x="10" y="11" width="10" height="8" fill="none" stroke="#333" stroke-width="1.4"/><path d="M12 14h6M12 16.5h6" stroke="#333" stroke-width="1.2"/></svg></span>Long-Term Memory<svg class="acc__chev" width="18" height="10"><path d="M1 1l8 7 8-7" stroke="#777" fill="none" stroke-width="1.5"/></svg></div>
    </div>
  </div>
</section>

</body>
</html>
```